Investment company needing business card

We are wanting a business card which looks sharp and easy on the eye. We are thinking of having a business card with the logo embossed on it, to really make it stand out. We will only have a small amount of information of the business card, person's name, position, email address and phone number

Contact Information for Business Card

Danielle Frost
Executive Assistant
+64 21 473 5162
danielf@harwickpartners.co.nz

Requirements
Must have
• Embossed logo
Should not have
• Not to be busy

```html
<!DOCTYPE html>
<html lang="en">
<head>
<meta charset="utf-8">
<title>Harwick Partners — Business Card</title>
<link href="https://fonts.googleapis.com/css2?family=Open+Sans:wght@400;700&display=swap" rel="stylesheet">
<style>
  :root {
    --backdrop: #e6e3e0;
    --card: #ffffff;
    --brand-green: #1ea866;
    --ink-grey: #555759;
    --soft-grey: #7a7c7e;
    --card-shadow: rgba(0, 0, 0, 0.14);
  }
  * { box-sizing: border-box; margin: 0; padding: 0; }
  html, body {
    width: 1200px;
    height: 997px;
    overflow: hidden;
    background: var(--backdrop);
    font-family: "Open Sans", sans-serif;
  }
  .sheet {
    width: 1200px;
    height: 997px;
    display: flex;
    flex-direction: column;
    align-items: center;
    justify-content: center;
    gap: 64px;
  }
  .card {
    position: relative;
    width: 600px;
    height: 333px;
    background: var(--card);
    box-shadow: 0 10px 28px var(--card-shadow);
  }
  .wordmark {
    display: flex;
    align-items: center;
    gap: 10px;
    color: var(--brand-green);
    font-weight: 700;
    text-transform: uppercase;
    letter-spacing: 0.06em;
    white-space: nowrap;
  }
  .wordmark__square {
    background: var(--brand-green);
    flex: none;
  }

  /* Contact side */
  .card--contact .wordmark {
    position: absolute;
    top: 38px;
    right: 40px;
    font-size: 22px;
  }
  .card--contact .wordmark__square { width: 22px; height: 22px; }
  .identity {
    position: absolute;
    top: 118px;
    left: 40px;
    padding-left: 18px;
    border-left: 7px solid var(--brand-green);
  }
  .identity__name {
    color: var(--brand-green);
    font-weight: 700;
    font-size: 17px;
    text-transform: uppercase;
    letter-spacing: 0.02em;
    line-height: 1.2;
  }
  .identity__role {
    color: var(--ink-grey);
    font-size: 14px;
    line-height: 1.4;
  }
  .contact-list {
    position: absolute;
    left: 132px;
    bottom: 44px;
    padding-left: 18px;
    border-left: 6px solid var(--brand-green);
    list-style: none;
  }
  .contact-list__item {
    display: flex;
    align-items: center;
    gap: 8px;
    color: var(--ink-grey);
    font-size: 14px;
    line-height: 1.55;
  }
  .contact-list__icon { width: 11px; height: 11px; flex: none; }

  /* Brand side */
  .card--brand .wordmark {
    position: absolute;
    top: 120px;
    left: 50%;
    transform: translateX(-50%);
    font-size: 36px;
  }
  .card--brand .wordmark__square { width: 36px; height: 36px; }
  .card--brand .website {
    position: absolute;
    right: 60px;
    bottom: 62px;
    color: var(--ink-grey);
    font-size: 16px;
    letter-spacing: 0.03em;
  }
</style>
</head>
<body>
<main class="sheet">
  <section class="card card--contact" aria-label="Business card, contact side">
    <div class="wordmark"><span class="wordmark__square"></span>Harwick Partners</div>
    <div class="identity">
      <p class="identity__name">Danielle Frost</p>
      <p class="identity__role">Executive Assistant</p>
    </div>
    <ul class="contact-list">
      <li class="contact-list__item">
        <svg class="contact-list__icon" viewBox="0 0 12 12" aria-hidden="true"><path fill="#1ea866" d="M2.4 0.8l1.8 2.2-1 1.2c0.7 1.6 2 2.9 3.6 3.6l1.2-1 2.2 1.8-1 2.2C4.8 10.6 1.4 7.2 0.2 2z"/></svg>
        +64 21 473 5162
      </li>
      <li class="contact-list__item">
        <svg class="contact-list__icon" viewBox="0 0 12 12" aria-hidden="true"><rect x="0.5" y="2" width="11" height="8" fill="#1ea866"/><path d="M0.8 2.4L6 6.6l5.2-4.2" fill="none" stroke="#fff" stroke-width="1"/></svg>
        danielf@harwickpartners.co.nz
      </li>
      <li class="contact-list__item">
        <svg class="contact-list__icon" viewBox="0 0 12 12" aria-hidden="true"><circle cx="6" cy="6" r="5.5" fill="#1ea866"/><path d="M0.8 6h10.4M6 0.6c-2.6 3-2.6 7.8 0 10.8M6 0.6c2.6 3 2.6 7.8 0 10.8" fill="none" stroke="#fff" stroke-width="0.8"/></svg>
        www.harwickpartners.co.nz
      </li>
    </ul>
  </section>

  <section class="card card--brand" aria-label="Business card, brand side">
    <div class="wordmark"><span class="wordmark__square"></span>Harwick Partners</div>
    <p class="website">www.harwickpartners.co.nz</p>
  </section>
</main>
</body>
</html>
```